Automotive component supplier needs a business card design

We need a business card design for our company called Velran Global Components Ltd based in the UK. We are a supplier of interior and exterior components to premium car manufacturers such as Corvel Ashby, Hadley Fenn, Marquist and Tavarelli. We would like to see a modern business card design that uses the colour blue.

Target Market(s)

Premium automotive car manufacturers.

Industry/Entity Type

Automotive

Contact Information for Business Card

Company Name : Velran Global Components Limited
Address: 17 Marlow Yard, Upper Heath, Warwick, CV31 8QL, United Kingdom
Web Address : www.velrancomponents-example.co.uk

Font styles to use
Other font styles liked:
• Helvetica

Colors
3176b5
0255a3
85acd3
cfdeed
cee9f5
85cae6
34a6d7
0692cd
9bcb3c

Requirements
Must have
• Clear company logo and a mixture of blue colours.
Nice to have
• A high quality modern image.
Should not have
• Multiple colours.

```html
<!DOCTYPE html>
<html lang="en">
<head>
<meta charset="utf-8">
<title>Velran Global Components – Business Card</title>
<link href="https://fonts.googleapis.com/css2?family=Arimo:wght@400;700&display=swap" rel="stylesheet">
<style>
  :root {
    --brand-blue: #0692cd;
    --card-blue: #0a8fd0;
    --deep-blue: #0255a3;
    --accent-green: #9bcb3c;
    --ink: #3a3a3a;
    --paper: #ffffff;
    --backdrop: #e9edf1;
  }
  * { box-sizing: border-box; margin: 0; padding: 0; }
  html, body { width: 1200px; height: 900px; overflow: hidden; }
  body {
    background: var(--backdrop);
    font-family: "Arimo", Helvetica, Arial, sans-serif;
    display: flex;
    align-items: center;
    justify-content: center;
    gap: 40px;
  }
  .card {
    position: relative;
    width: 540px;
    height: 309px;
    border-radius: 22px;
    overflow: hidden;
    box-shadow: 0 6px 18px rgba(0,0,0,0.12);
  }

  /* Front: contact side */
  .card--front { background: var(--paper); color: var(--ink); }
  .wordmark {
    position: absolute;
    font-weight: 700;
    white-space: nowrap;
  }
  .card--front .wordmark { left: 34px; top: 30px; color: var(--brand-blue); }
  .wordmark__name { display: block; font-size: 40px; line-height: 1; letter-spacing: 1px; text-transform: uppercase; }
  .wordmark__line { display: block; font-size: 12px; letter-spacing: 2.4px; margin-top: 6px; text-transform: uppercase; }

  .address {
    position: absolute;
    left: 34px; top: 128px;
    display: flex; gap: 10px;
    font-size: 11.5px; line-height: 1.45;
  }
  .address svg { flex: none; margin-top: 1px; }

  .person { position: absolute; right: 34px; top: 150px; text-align: right; }
  .person__name { font-size: 25px; font-weight: 700; color: var(--accent-green); letter-spacing: 0.5px; text-transform: uppercase; white-space: nowrap; }
  .person__role { font-size: 12px; font-weight: 700; color: var(--brand-blue); letter-spacing: 1px; margin-top: 4px; text-transform: uppercase; }

  .contacts {
    position: absolute; right: 34px; bottom: 26px;
    list-style: none;
    font-size: 11.5px; line-height: 1.6;
    text-align: right;
  }
  .contacts li { display: flex; justify-content: flex-end; align-items: center; gap: 8px; white-space: nowrap; }
  .contacts svg { flex: none; }

  /* Back: brand side */
  .card--back { background: var(--card-blue); }
  .card--back .frame {
    position: absolute; inset: 14px;
    border: 1px solid var(--accent-green);
    border-radius: 12px;
  }
  .card--back .wordmark {
    left: 50%; top: 50%;
    transform: translate(-50%, -50%);
    color: var(--paper);
    text-align: center;
  }
  .card--back .wordmark__name { font-size: 66px; letter-spacing: 2px; }
  .card--back .wordmark__line { font-size: 17px; letter-spacing: 4px; margin-top: 8px; }
</style>
</head>
<body>

  <section class="card card--front" aria-label="Business card, contact side">
    <div class="wordmark">
      <span class="wordmark__name">Velran</span>
      <span class="wordmark__line">Global Components</span>
    </div>

    <p class="address">
      <svg width="18" height="14" viewBox="0 0 18 14" aria-hidden="true">
        <path d="M1 6 L17 1 L10 13 L8 8 Z M8 8 L17 1" fill="none" stroke="var(--accent-green)" stroke-width="1.4" stroke-linejoin="round"/>
      </svg>
      <span>17 Marlow Yard, Upper Heath,<br>Warwick, CV31 8QL, UK</span>
    </p>

    <div class="person">
      <p class="person__name">Daniel Hartwell</p>
      <p class="person__role">CEO/Founder</p>
    </div>

    <ul class="contacts">
      <li>012-555-0148
        <svg width="12" height="12" viewBox="0 0 12 12" aria-hidden="true"><path d="M3 1 L5 3.5 L4 5 Q5.5 7.5 7 8 L8.5 7 L11 9 L9.5 11 Q4 10.5 1 3 Z" fill="var(--brand-blue)"/></svg>
      </li>
      <li>012-555-0148
        <svg width="12" height="12" viewBox="0 0 12 12" aria-hidden="true"><rect x="3" y="0.7" width="6" height="10.6" rx="1" fill="none" stroke="var(--brand-blue)" stroke-width="1.3"/><circle cx="6" cy="9.4" r="0.7" fill="var(--brand-blue)"/></svg>
      </li>
      <li>d.hartwell@velranmail-example.co.uk
        <svg width="12" height="12" viewBox="0 0 12 12" aria-hidden="true"><rect x="0.5" y="2" width="11" height="8" fill="var(--brand-blue)"/><path d="M0.8 2.4 L6 6.6 L11.2 2.4" fill="none" stroke="#fff" stroke-width="1"/></svg>
      </li>
      <li>www.velrancomponents-example.co.uk
        <svg width="12" height="12" viewBox="0 0 12 12" aria-hidden="true"><circle cx="6" cy="6" r="5.5" fill="var(--brand-blue)"/><path d="M0.5 6 H11.5 M6 0.5 V11.5 M6 0.5 Q2.5 6 6 11.5 M6 0.5 Q9.5 6 6 11.5" fill="none" stroke="#fff" stroke-width="0.7"/></svg>
      </li>
    </ul>
  </section>

  <section class="card card--back" aria-label="Business card, brand side">
    <div class="frame"></div>
    <div class="wordmark">
      <span class="wordmark__name">Velran</span>
      <span class="wordmark__line">Global Components</span>
    </div>
  </section>

</body>
</html>
```